design a construction company business card

Design business card around our logo. Card must have all the typical info: name, title, address, phone, email, business name, etc. Somewhere on the card I would like to see our motto "Built with care... Driven by lasting quality." Consider adding a splash of bright orange to the card to complement the blues and silvers/grays in the logo. We are open to metallic inks, textures, etc. We would like to see options on both light and dark backgrounds. The font in the logo is Euro Technic Extended Regular.

```html
<!DOCTYPE html>
<html lang="en">
<head>
<meta charset="utf-8">
<title>Halden Contracting – Business Card</title>
<link rel="stylesheet" href="https://fonts.googleapis.com/css2?family=Michroma&family=Exo+2:wght@400;500&display=swap">
<style>
  :root {
    --backdrop: #3a3a3c;
    --card-front: #202022;
    --card-back: #29292b;
    --skyline-shade: #303033;
    --brand-blue: #2f7fd8;
    --text-light: #dcdde0;
    --text-muted: #a3a5aa;
  }
  * { margin: 0; padding: 0; box-sizing: border-box; }
  html, body {
    width: 1200px; height: 1000px; overflow: hidden;
    background: var(--backdrop);
  }
  .canvas { position: relative; width: 1200px; height: 1000px; }
  .card {
    position: absolute; width: 640px; height: 366px;
    border-radius: 28px; overflow: hidden;
    box-shadow: 0 18px 40px rgba(0,0,0,.45);
  }
  .card--front { left: 460px; top: 70px; background: var(--card-front); }
  .card--back { left: 100px; top: 540px; background: var(--card-back); }

  .wordmark { text-align: center; font-family: "Michroma", sans-serif; }
  .wordmark__name {
    display: flex; align-items: center; justify-content: center; gap: 16px;
    font-size: 58px; letter-spacing: 4px; color: var(--brand-blue); line-height: 1;
  }
  .wordmark__mark { width: 18px; height: 18px; background: var(--brand-blue); flex: none; }
  .wordmark__sub {
    margin-top: 12px; font-size: 17px; letter-spacing: 2px; color: var(--brand-blue);
  }

  .card--front .wordmark { position: absolute; left: 0; right: 0; top: 112px; }
  .motto {
    position: absolute; left: 0; right: 0; top: 272px; text-align: center;
    font-family: "Michroma", sans-serif; font-size: 13px; letter-spacing: 1px;
    color: var(--brand-blue);
  }

  .skyline-shade {
    position: absolute; left: 40px; top: 40px; width: 300px; height: 326px;
    background: linear-gradient(90deg, rgba(48,48,51,0) 0%, var(--skyline-shade) 40%, rgba(48,48,51,0) 100%);
  }

  .person { position: absolute; left: 44px; top: 158px; }
  .person__name {
    font-family: "Michroma", sans-serif; font-size: 22px; font-weight: 400; color: var(--brand-blue);
  }
  .person__title {
    margin-top: 6px; font-family: "Exo 2", sans-serif; font-size: 15px; color: var(--text-muted);
  }

  .card--back .wordmark { position: absolute; right: 44px; top: 62px; width: 300px; }
  .card--back .wordmark__name { font-size: 38px; gap: 10px; letter-spacing: 2px; }
  .card--back .wordmark__mark { width: 12px; height: 12px; }
  .card--back .wordmark__sub { font-size: 12px; margin-top: 8px; }

  .contact {
    position: absolute; right: 40px; top: 206px; text-align: right;
    font-family: "Exo 2", sans-serif; font-size: 17px; line-height: 1.4; color: var(--text-light);
    list-style: none;
  }
  .contact__row { display: flex; justify-content: flex-end; align-items: center; gap: 10px; }
  .contact__row--address { padding-right: 26px; }
  .contact__icon { width: 16px; height: 16px; flex: none; }
  .contact__accent { color: var(--brand-blue); }
</style>
</head>
<body>
<main class="canvas">
  <section class="card card--front" aria-label="Card front">
    <div class="wordmark">
      <div class="wordmark__name"><span class="wordmark__mark"></span>HALDEN</div>
      <div class="wordmark__sub">CONTRACTING, INC.</div>
    </div>
    <p class="motto">BUILT WITH CARE... DRIVEN BY LASTING QUALITY.</p>
  </section>

  <section class="card card--back" aria-label="Card back">
    <div class="skyline-shade" role="img" aria-label="Faint building silhouettes in dark grey"></div>
    <div class="person">
      <h1 class="person__name">Marcus Reyes</h1>
      <p class="person__title">Managing Director</p>
    </div>
    <div class="wordmark">
      <div class="wordmark__name"><span class="wordmark__mark"></span>HALDEN</div>
      <div class="wordmark__sub">CONTRACTING, INC.</div>
    </div>
    <ul class="contact">
      <li class="contact__row contact__row--address">4820 Ridge Avenue</li>
      <li class="contact__row contact__row--address">Brookfield NY 10233</li>
      <li class="contact__row">555.014.2290
        <svg class="contact__icon" viewBox="0 0 16 16"><circle cx="8" cy="8" r="8" fill="#2f7fd8"/><path d="M5.5 4.2l1.4 1.6-.7 1a5 5 0 0 0 3 3l1-.7 1.6 1.4-.8 1.2C8 12.6 3.4 8 3.8 5z" fill="#29292b"/></svg>
      </li>
      <li class="contact__row">marcus@haldenbuild.com
        <svg class="contact__icon" viewBox="0 0 16 16"><circle cx="8" cy="8" r="8" fill="#2f7fd8"/><rect x="4" y="5" width="8" height="6" fill="none" stroke="#29292b" stroke-width="1.2"/><path d="M4 5l4 3.2L12 5" fill="none" stroke="#29292b" stroke-width="1.2"/></svg>
      </li>
      <li class="contact__row"><span>www.<span class="contact__accent">haldenbuild</span>.com</span>
        <svg class="contact__icon" viewBox="0 0 16 16"><circle cx="8" cy="8" r="8" fill="#2f7fd8"/><circle cx="8" cy="8" r="4.2" fill="none" stroke="#29292b" stroke-width="1.1"/><path d="M3.8 8h8.4M8 3.8c-2 2.5-2 5.9 0 8.4M8 3.8c2 2.5 2 5.9 0 8.4" fill="none" stroke="#29292b" stroke-width="1"/></svg>
      </li>
    </ul>
  </section>
</main>
</body>
</html>
```